Group training gym/bootcamp needs a web design

We need a website for our gym that is based in Sydney. We have indoor functional training classes and outdoor bootcamp classes. We would like the web site to have a video (to be created) and photo gallery. I would like the site made on word press and i would like to be able to make minor changes such as changing images and text without having to use a designer.

The website should have the following pages: home page; the gym; the bootcamp; photo gallery; about us; contact.

I have uploaded our logo and i would like to keep to these colour (blue,yellow,silver) and black is also allowed

Target Market(s)

18-50 male and female

Industry/Entity Type

Gym

Coding

Coded - Design and coding required

Number of Pages Required

5+ page

Font styles to use
Sans Serif

Colors
0692cd
fbed22
1b1b1b
e8e8e8

Requirements
Must have
• The website should have the following pages: home page; the gym; the bootcamp; photo gallery; about us; contact.
• I have uploaded our logo and i would like to keep to these colour (blue,yellow,silver) and black is also allowed
• Video upload and photo upload

```html
<!DOCTYPE html>
<html lang="en">
<head>
<meta charset="utf-8">
<title>Ironbark Fitness Station – Functional Training Classes</title>
<link href="https://fonts.googleapis.com/css2?family=Raleway:wght@500;600;700;800&family=Open+Sans:wght@400;600;700&display=swap" rel="stylesheet">
<style>
:root{
  --blue:#0692cd;
  --yellow:#fbed22;
  --black:#1b1b1b;
  --silver:#e8e8e8;
  --grey-bg:#efefef;
  --text:#555;
  --white:#fff;
}
*{box-sizing:border-box;margin:0;padding:0}
html,body{width:1200px;height:3340px;overflow:hidden;background:var(--white)}
body{font-family:"Open Sans",Arial,sans-serif;color:var(--text)}
.page{position:relative;width:1200px;height:3340px;overflow:hidden}
.photo{position:absolute}

/* header */
.site-header{position:absolute;left:0;top:0;width:1200px;height:123px;background:var(--white);z-index:2}
.brand{position:absolute;left:160px;top:40px;display:flex;align-items:center;gap:10px}
.brand-mark{width:34px;height:34px;background:var(--blue);border-radius:50%}
.brand-name{font-family:"Raleway",sans-serif;font-weight:800;font-size:17px;line-height:19px;color:var(--blue);text-transform:uppercase}
.call{position:absolute;left:784px;top:29px;font-family:"Raleway",sans-serif;font-weight:700;font-size:15px;color:var(--black)}
.login{position:absolute;left:964px;top:23px;width:74px;height:32px;border:2px solid var(--blue);color:var(--blue);font-family:"Raleway",sans-serif;font-weight:700;font-size:12px;display:flex;align-items:center;justify-content:center}
.main-nav{position:absolute;left:378px;top:81px;display:flex;font-family:"Raleway",sans-serif;font-weight:700;font-size:12.5px;color:var(--black)}
.main-nav span{margin-right:40px}
.main-nav span:last-child{margin-right:0}
.main-nav .active{color:var(--blue)}
.search{position:absolute;left:1026px;top:82px}

/* hero */
.hero{position:absolute;left:0;top:123px;width:1200px;height:518px;background:linear-gradient(110deg,#3c3a36 0%,#6b6550 30%,#c9b63a 45%,#8c7b46 60%,#45423c 100%)}
.hero-title{position:absolute;left:160px;top:294px;font-family:"Raleway",sans-serif;font-weight:800;font-size:34px;line-height:42px;color:var(--white);text-transform:uppercase}
.hero-title em{font-style:normal;color:var(--yellow)}
.hero-dots{position:absolute;left:514px;top:594px;display:flex;gap:6px}
.hero-dots i{display:block;width:34px;height:4px;background:rgba(255,255,255,.55)}
.hero-dots i.on{background:var(--yellow)}

.bands{position:absolute;left:0;top:641px}

/* feature blocks */
.feature{position:absolute;width:450px}
.feature-title{font-family:"Raleway",sans-serif;font-weight:700;font-size:23px;line-height:35px;color:var(--black);text-transform:uppercase;letter-spacing:.5px}
.feature-text{margin-top:14px;font-size:10.5px;line-height:22px;color:var(--text)}
.btn{margin-top:20px;width:112px;height:40px;background:var(--yellow);color:var(--black);font-family:"Raleway",sans-serif;font-weight:700;font-size:12px;display:flex;align-items:center;justify-content:center;text-transform:uppercase}

.section-title{position:absolute;left:0;width:1200px;text-align:center;font-family:"Raleway",sans-serif;font-weight:700;font-size:24px;color:var(--black);text-transform:uppercase;letter-spacing:.5px}
.section-intro{position:absolute;left:240px;width:720px;text-align:center;font-size:11px;line-height:22px}
.play{position:absolute;width:64px;height:64px}

.card-img{position:absolute;width:274px;height:194px}
.card-bar{position:absolute;width:274px;height:6px;background:var(--yellow)}
.card-title{position:absolute;font-family:"Raleway",sans-serif;font-weight:700;font-size:15px;color:var(--black);text-transform:uppercase}
.card-text{position:absolute;width:274px;font-size:11px;line-height:22px}

/* testimonial */
.testimonial{position:absolute;left:270px;top:2772px;width:660px;text-align:center}
.quote{font-family:"Raleway",sans-serif;font-weight:700;font-size:18px;line-height:32px;color:var(--black)}
.quote b{font-size:30px;line-height:0;vertical-align:-8px;font-family:"Open Sans",sans-serif}
.quote-name{margin-top:22px;font-weight:700;font-size:12px;color:var(--black)}

/* footer */
.site-footer{position:absolute;left:0;top:2975px;width:1200px;height:365px;background:var(--black);color:#cfcfcf}
.signup-label{position:absolute;left:163px;top:40px;font-family:"Raleway",sans-serif;font-weight:700;font-size:18px;color:var(--white);text-transform:uppercase}
.signup-input{position:absolute;left:624px;top:31px;width:327px;height:40px;background:#3a3a3a;color:#9a9a9a;font-size:11px;padding:0 12px;display:flex;align-items:center}
.signup-btn{position:absolute;left:951px;top:31px;width:87px;height:40px;background:var(--yellow);color:var(--black);font-family:"Raleway",sans-serif;font-weight:700;font-size:12px;display:flex;align-items:center;justify-content:center}
.footer-rule{position:absolute;left:160px;top:94px;width:880px;height:1px;background:#3a3a3a}
.footer-col{position:absolute;top:125px}
.footer-col h4{font-family:"Raleway",sans-serif;font-weight:700;font-size:12px;color:var(--yellow);text-transform:uppercase;margin-bottom:14px}
.footer-col p{font-size:11px;line-height:22px;color:#cfcfcf}
.copyright{position:absolute;left:163px;top:308px;font-size:10.5px;color:#cfcfcf}
.social{position:absolute;left:858px;top:302px;display:flex;gap:14px}
.social i{display:block;width:16px;height:16px;border-radius:50%;background:var(--white)}
</style>
</head>
<body>
<div class="page">

  <svg class="bands" width="1200" height="2334" viewBox="0 0 1200 2334" aria-hidden="true">
    <rect x="0" y="0" width="1200" height="960" fill="#efefef"/>
    <polygon points="0,120 1200,0 1200,340 0,620" fill="#f4f4f4"/>
    <polygon points="0,951 1200,784 1200,1520 0,1520" fill="#ffffff"/>
    <polygon points="0,1589 1200,1500 1200,2334 0,2334" fill="#efefef"/>
    <polygon points="0,2087 1200,1976 1200,2334 0,2334" fill="#fbed22"/>
  </svg>

  <header class="site-header">
    <div class="brand">
      <span class="brand-mark"></span>
      <span class="brand-name">Ironbark<br>Fitness Station</span>
    </div>
    <div class="call">CALL US: 555-010-2290</div>
    <div class="login">LOGIN</div>
    <nav class="main-nav">
      <span class="active">HOME</span><span>THE GYM</span><span>THE BOOTCAMP</span><span>PHOTO GALLERY</span><span>ABOUT US</span><span>CONTACT US</span>
    </nav>
    <svg class="search" width="13" height="13" viewBox="0 0 13 13" aria-hidden="true"><circle cx="5.5" cy="5.5" r="4" fill="none" stroke="#1b1b1b" stroke-width="2"/><line x1="8.5" y1="8.5" x2="12" y2="12" stroke="#1b1b1b" stroke-width="2"/></svg>
  </header>

  <section class="hero" role="img" aria-label="Woman doing a barbell squat in the gym with a trainer spotting her, yellow tinted"></section>
  <h1 class="hero-title">Functional<br>Training <em>Classes</em></h1>
  <div class="hero-dots"><i class="on"></i><i></i><i></i></div>

  <!-- indoor -->
  <div class="feature" style="left:160px;top:714px">
    <h2 class="feature-title">Indoor Functional<br>Training Classes</h2>
    <p class="feature-text">Sed ut perspiciatis unde omnis iste natus sitolu platem accusantium doloremque lantium, totme maperiam, eaque ipsa quae ab illo inventore veritati quasi archite ed ut perspiciatis unde omnis iste natus sitolu platem accusantium doloremque laudant ium,totmem aperi amaque ipsa quae ab illo inventore veritati quasiar hit ecterspiciatis unde omnis iste natus sitolu,maque ipsa quae ab illo inventoretotme maperiam, eaque ipsa quae ab illo inventore veritati quasi archite ed ut perspiciatis unde omnis iste natus sitolu platem accusantium doloremque laudant ium,totmem aperi amaque isaua.</p>
    <div class="btn">Read More</div>
  </div>
  <div class="photo" style="left:664px;top:690px;width:374px;height:350px;background:linear-gradient(150deg,#d9d9d9,#8f8f8f 55%,#4a4a4a)" role="img" aria-label="Group doing kettlebell lunges in an indoor class"></div>

  <!-- outdoor -->
  <div class="photo" style="left:160px;top:1098px;width:372px;height:350px;background:linear-gradient(160deg,#6f8f3e,#a8c25a 45%,#7a3d6a 75%,#3f5a24)" role="img" aria-label="People doing sit-ups on mats in a park"></div>
  <div class="feature" style="left:597px;top:1123px;width:443px">
    <h2 class="feature-title">Outdoor<br>Bootcamp Classes</h2>
    <p class="feature-text">Sed ut perspiciatis unde omnis iste natus sitolu platem accusantium doloremque lantium, totme maperiam, eaque ipsa quae ab illo inventore veritati quasi archite ed ut perspiciatis unde omnis iste natus sitolu platem accusantium doloremque laudant ium,totmem aperi amaque ipsa quae ab illo inventore veritati quasiar hit ecterspiciatis unde omnis iste natus sitolu,maque ipsa quae ab illo inventoretotme maperiam, eaque ipsa quae ab illo inventore veritati quasi archite ed ut perspiciatis unde omnis iste natus sitolu platem accusantium doloremque laudant ium,totmem aperi amaque isaua.</p>
    <div class="btn">Read More</div>
  </div>

  <!-- gallery -->
  <h2 class="section-title" style="top:1584px">Video &amp; Photo Gallery</h2>
  <p class="section-intro" style="top:1624px">Sed ut perspiciatis unde omnis iste natus sitolu platem accusantium doloremque lantium, totme maperiam, eaque ipsa quae ab illo inventore veritati quasiar hit ecterspiciatis unde omnis iste natus sitolu,maque ipsa quae ab illo inventoretotme maperiam, eaque ipsa quae.</p>

  <div class="photo" style="left:160px;top:1690px;width:357px;height:216px;background:linear-gradient(120deg,#e8e2d6,#a99880 55%,#5d5349)" role="img" aria-label="Video: woman doing push-ups with a trainer"></div>
  <div class="photo" style="left:521px;top:1690px;width:279px;height:216px;background:linear-gradient(140deg,#cfc8c0,#b07a78 50%,#6c5c58)" role="img" aria-label="Two women training with a medicine ball"></div>
  <div class="photo" style="left:806px;top:1690px;width:232px;height:216px;background:linear-gradient(140deg,#7fa3c4,#3f6f9a 55%,#243a52)" role="img" aria-label="Man doing a lunge on a blue background"></div>
  <div class="photo" style="left:160px;top:1911px;width:277px;height:216px;background:linear-gradient(140deg,#bdbdbd,#8a8a8a 50%,#5a4e44)" role="img" aria-label="Two people doing box jumps"></div>
  <div class="photo" style="left:443px;top:1911px;width:234px;height:216px;background:linear-gradient(140deg,#3d3a36,#6e6760 50%,#2a2825)" role="img" aria-label="Close-up of dumbbells on a gym floor"></div>
  <div class="photo" style="left:684px;top:1911px;width:354px;height:216px;background:linear-gradient(140deg,#9a9a7a,#c8c25a 45%,#5d6b3f)" role="img" aria-label="Video: men training with suspension straps"></div>

  <svg class="play" style="left:306px;top:1766px" viewBox="0 0 64 64" aria-hidden="true"><circle cx="32" cy="32" r="29" fill="none" stroke="#fff" stroke-width="4"/><polygon points="25,19 47,32 25,45" fill="#fff"/></svg>
  <svg class="play" style="left:829px;top:1987px" viewBox="0 0 64 64" aria-hidden="true"><circle cx="32" cy="32" r="29" fill="none" stroke="#fff" stroke-width="4"/><polygon points="25,19 47,32 25,45" fill="#fff"/></svg>

  <!-- what we do -->
  <h2 class="section-title" style="top:2205px">What We Do</h2>

  <div class="card-img" style="left:160px;top:2267px;background:linear-gradient(150deg,#6a6a6a,#2e2e2e 60%,#151515)" role="img" aria-label="Muscular man with dumbbells in a dark gym"></div>
  <div class="card-bar" style="left:160px;top:2461px"></div>
  <h3 class="card-title" style="left:160px;top:2494px">Bonorumaloru Loper</h3>
  <p class="card-text" style="left:160px;top:2522px">Sed ut perspiciatis unde omnis iste natusdor sitolu platem accusantium doloremque laudantium, totm e maperiam, eaque ipsa quaeillsed ut perspiciatis unde omnis iste natus sitolu platem.</p>

  <div class="card-img" style="left:463px;top:2267px;background:linear-gradient(150deg,#b5684e,#8a5a46 50%,#3e3a36)" role="img" aria-label="Woman training with battle ropes against a brick wall"></div>
  <div class="card-bar" style="left:463px;top:2461px"></div>
  <h3 class="card-title" style="left:463px;top:2494px">Bonorumaloru Loper</h3>
  <p class="card-text" style="left:463px;top:2522px">Sed ut perspiciatis unde omnis iste natusdor sitolu platem accusantium doloremque laudantium, totm e maperiam, eaque ipsa quaeillsed ut perspiciatis unde omnis iste natus sitolu platem .</p>

  <div class="card-img" style="left:764px;top:2267px;background:linear-gradient(180deg,#8fb3d9,#b9cfe0 45%,#6f9a4a 70%,#4d7a33)" role="img" aria-label="Outdoor group exercising on a sports field"></div>
  <div class="card-bar" style="left:764px;top:2461px"></div>
  <h3 class="card-title" style="left:764px;top:2494px">Bonorumaloru Loper</h3>
  <p class="card-text" style="left:764px;top:2522px">Sed ut perspiciatis unde omnis iste natusdor sitolu platem accusantium doloremque laudantium, totm e maperiam, eaque ipsa quaeillsed ut perspiciatis unde omnis iste natus sitolu platem .</p>

  <!-- testimonial -->
  <figure class="testimonial">
    <blockquote class="quote"><b>&#8220;</b> Sed ut perspiciatis unde omnis iste natus error sit voluptaem audantium, totam rem aperiam, eaquem accusantium doloree lada ntium, totam rem aperiam, eaque ipsa quae ab illo inventore. <b>&#8221;</b></blockquote>
    <figcaption class="quote-name">Alex Rowan, City Name</figcaption>
  </figure>

  <!-- footer -->
  <footer class="site-footer">
    <div class="signup-label">Sign up for the latest news and offers</div>
    <div class="signup-input">Enter Email Address</div>
    <div class="signup-btn">SIGN UP</div>
    <div class="footer-rule"></div>

    <div class="footer-col" style="left:163px"><h4>Nav</h4><p>Home<br>The Gym<br>The Bootcamp<br>Photo Gallery<br>About us</p></div>
    <div class="footer-col" style="left:365px"><h4>Classes</h4><p>Bootcamp<br>Training classes<br>Indoor<br>Outdoor</p></div>
    <div class="footer-col" style="left:552px"><h4>Company</h4><p>Lorem sum<br>Folor sit amet<br>Consectet<br>Voluptatem</p></div>
    <div class="footer-col" style="left:708px"><h4>Help</h4><p>Terms<br>Privacy<br>Contact us</p></div>
    <div class="footer-col" style="left:860px"><h4>Contact Us</h4><p>48 Harbour Lane Suite 12<br>Surry Hills, Sydney, 2010<br>Phone: (555) 010-7731</p></div>

    <div class="copyright">© 2017 Functional Training Classes. All Copyrights are Reserved. Terms of Use.</div>
    <div class="social" aria-label="Social links"><i></i><i></i><i></i><i></i><i></i><i></i></div>
  </footer>

</div>
</body>
</html>
```